Brightfield Ventures Inc. Letterhead

Creation of attractive and eye catching letterhead for a business start-up for the construction industry. Letterhead must relate to construction, but avoid standard hammer and tools in the design.

I forgot to add some details, sorry about that. Some pertinent info: Ph: 916-555-0187 brightfieldventures.example 448 Willowmere Ave, Ste 210 Folsom, CA 95999 info@brightfieldventures.example not sure if slogan should be in there" “Connecting construction professionals to create a purpose driven industry.” must be able to be used in word. Thanks!

```html
<!DOCTYPE html>
<html lang="en">
<head>
<meta charset="utf-8">
<title>Brightfield Ventures Inc. Letterhead</title>
<link href="https://fonts.googleapis.com/css2?family=Lato:wght@400;700;900&family=Kaushan+Script&display=swap" rel="stylesheet">
<style>
  :root {
    --navy: #1d2160;
    --navy-deep: #151848;
    --red: #d3242b;
    --paper: #ffffff;
    --ink: #3a3a4a;
    --muted: #c9cbe0;
  }
  * { margin: 0; padding: 0; box-sizing: border-box; }
  html, body { width: 882px; height: 1200px; overflow: hidden; background: var(--paper); }
  .letterhead {
    position: relative;
    width: 882px;
    height: 1200px;
    background: var(--paper);
    font-family: "Lato", Arial, sans-serif;
    color: var(--ink);
  }
  .header-band, .footer-band { position: absolute; left: 0; width: 882px; display: block; }
  .header-band { top: 0; height: 230px; }
  .footer-band { bottom: 0; height: 190px; }

  .contact-list {
    position: absolute;
    top: 26px;
    left: 62px;
    list-style: none;
    color: var(--muted);
    font-size: 11px;
    line-height: 17px;
    letter-spacing: 0.2px;
  }
  .contact-list li { display: flex; align-items: center; gap: 7px; }
  .contact-list svg { width: 10px; height: 10px; fill: var(--muted); }

  .brand {
    position: absolute;
    top: 250px;
    right: 74px;
    display: flex;
    align-items: center;
    gap: 10px;
  }
  .brand-mark { width: 22px; height: 22px; background: var(--red); }
  .brand-name {
    font-weight: 900;
    color: var(--navy);
    font-size: 21px;
    line-height: 22px;
    letter-spacing: 1px;
    text-transform: uppercase;
    text-align: left;
  }

  .letter-body {
    position: absolute;
    top: 405px;
    left: 94px;
    width: 694px;
    font-size: 13.5px;
    line-height: 20px;
  }
  .salutation { font-weight: 700; color: var(--navy); margin-bottom: 20px; }
  .letter-body p.paragraph { margin-bottom: 20px; text-align: justify; }
  .closing { margin-top: 30px; color: var(--navy); font-size: 14px; }
  .signature {
    font-family: "Kaushan Script", cursive;
    color: var(--navy);
    font-size: 26px;
    margin-top: 4px;
  }

  .footer-address {
    position: absolute;
    right: 74px;
    bottom: 34px;
    text-align: right;
    color: #ffffff;
    font-size: 11.5px;
    line-height: 17px;
  }
</style>
</head>
<body>
<main class="letterhead">

  <svg class="header-band" viewBox="0 0 882 230" preserveAspectRatio="none" aria-hidden="true">
    <path d="M0 0 H882 V40 C700 40 520 130 0 118 Z" fill="var(--navy)"/>
    <path d="M0 118 C520 130 700 40 882 40 V52 C700 58 520 150 0 132 Z" fill="var(--red)"/>
    <path d="M0 140 C420 160 680 80 882 62 V66 C680 90 420 168 0 146 Z" fill="var(--navy)"/>
  </svg>

  <ul class="contact-list">
    <li><svg viewBox="0 0 10 10"><path d="M2 0 L4 2.5 L3 3.6 Q4.2 5.8 6.4 7 L7.5 6 L10 8 L8.5 10 Q2 9 0 1.5 Z"/></svg>Ph: 916-555-0187</li>
    <li><svg viewBox="0 0 10 10"><path d="M0 2 H10 V8 H0 Z M0 2 L5 6 L10 2" stroke="#1d2160" stroke-width="0.8"/></svg>info@brightfieldventures.example</li>
    <li><svg viewBox="0 0 10 10"><circle cx="5" cy="5" r="4.5"/></svg>brightfieldventures.example</li>
  </ul>

  <div class="brand">
    <span class="brand-mark"></span>
    <span class="brand-name">Brightfield<br>Ventures</span>
  </div>

  <section class="letter-body">
    <p class="salutation">Dear Mr. Lorem,</p>
    <p class="paragraph">Lorem ipsum dolor sit amet, consectetuer adipiscing elit, sed diam nonummy nibh euismod tincidunt ut laoreet dolore magna aliquam erat volutpat. Ut wisi enim ad minim veniam, quis nostrud exerci tation ullamcorper suscipit lobortis nisl ut aliquip ex ea commodo consequat. Duis autem vel eum iriure dolor in hendrerit in vulputate velit esse molestie consequat, vel illum dolore eu feugiat nulla facilisis.</p>
    <p class="paragraph">Lorem ipsum dolor sit amet, consectetuer adipiscing elit, sed diam nonummy nibh euismod tincidunt ut laoreet dolore magna aliquam erat volutpat. Ut wisi enim ad minim veniam, quis nostrud exerci tation ullamcorper suscipit lobortis nisl ut aliquip ex ea commodo consequat. Duis autem vel eum iriure dolor in hendrerit in vulputate velit esse molestie consequat, vel illum dolore eu feugiat nulla facilisis.</p>
    <p class="paragraph">Lorem ipsum dolor sit amet, consectetuer adipiscing elit, sed diam nonummy nibh euismod tincidunt ut laoreet dolore magna aliquam erat volutpat. Ut wisi enim ad minim veniam, quis nostrud exerci tation ullamcorper suscipit lobortis nisl ut aliquip ex ea commodo consequat. Duis autem vel eum iriure dolor in hendrerit in vulputate velit esse molestie consequat, vel illum dolore eu feugiat nulla facilisis.</p>
    <p class="closing">Sincerely Your,</p>
    <p class="signature">Your Name</p>
  </section>

  <svg class="footer-band" viewBox="0 0 882 190" preserveAspectRatio="none" aria-hidden="true">
    <path d="M0 20 C200 10 360 110 560 96 C700 86 800 50 882 30 V36 C800 60 700 96 560 106 C360 120 200 22 0 28 Z" fill="var(--navy)"/>
    <path d="M0 40 C200 30 360 128 560 116 C700 106 800 72 882 50 V64 C800 86 700 120 560 130 C360 142 200 50 0 56 Z" fill="var(--red)"/>
    <path d="M0 64 C200 58 360 150 560 140 C700 132 800 98 882 74 V190 H0 Z" fill="var(--navy)"/>
  </svg>

  <address class="footer-address" style="font-style: normal;">
    448 Willowmere Ave, Ste 210<br>
    Folsom, CA 95999
  </address>

</main>
</body>
</html>
```